Candle Rental Business seeks new website design

We need a new website design for a Candle hire business. The business rents out pillar candles for events such as weddings and corporate events. Our main target market is weddings. The business name is Hire a Lantern. The business name does not have a logo design.

We would like a website that is light in colours and creates a warm atmosphere. The design needs to be elegant and upmarket. There are different size candles that we hire out, ranging from 10cm diameter to 20cm diameter, flat, tall etc. All our candles are white in colour. Its just the size that differs.

We would also like to include a section for hiring out decor such as glassvases, candlebras, overlays and chairs sachets, chair covers. However, this is not the businesses main focus but an additional offering to customers.

Target Market(s)

Wedding venues and brides. Corporate events. School dances.

Industry/Entity Type

Hospitality

Logo Text

Hire a Lantern

Number of Pages Required

1 page

Font styles to use
Sans Serif
Script

Requirements
Must have
• Pictures of pillar candles. Plain white candles. The website must centre around candles.
Nice to have
• Different examples of candle centrepieces
Should not have
• Pictures must not be of brides. Pictures of surrounding is perferable.

```html
<!DOCTYPE html>
<html lang="en">
<head>
<meta charset="utf-8">
<title>Hire a Lantern — Pillar Candle Hire</title>
<link rel="stylesheet" href="https://fonts.googleapis.com/css2?family=Raleway:ital,wght@0,400;0,500;0,600;0,700;1,400&display=swap">
<style>
  :root {
    --pink: #ea7479;
    --pink-soft: #f9a3a8;
    --pink-nav-top: #fba7ac;
    --pink-nav-bottom: #f38d94;
    --ink: #333333;
    --ink-soft: #555555;
    --grey-band: #f3f3f3;
    --footer: #343434;
    --footer-text: #d9d9d9;
    --white: #ffffff;
    --btn-top: #3d3d3d;
    --btn-bottom: #050505;
  }
  * { box-sizing: border-box; margin: 0; padding: 0; }
  html, body { width: 1200px; height: 2507px; overflow: hidden; }
  body {
    position: relative;
    background: var(--white);
    font-family: "Raleway", Arial, sans-serif;
    color: var(--ink);
  }
  .abs { position: absolute; }

  /* Header */
  .brand { left: 75px; top: 26px; font-size: 36px; font-weight: 600; color: var(--ink-soft); letter-spacing: .3px; }
  .phone { right: 75px; top: 32px; font-size: 21px; font-weight: 600; color: var(--ink-soft); display: flex; align-items: center; gap: 16px; }
  .nav {
    left: 0; top: 92px; width: 1200px; height: 55px;
    background: linear-gradient(var(--pink-nav-top), var(--pink-nav-bottom));
  }
  .nav ul { list-style: none; display: flex; margin-left: 75px; height: 100%; }
  .nav li { color: var(--white); font-size: 14.5px; font-weight: 500; padding: 0 30px; line-height: 55px; }
  .nav li.is-active { background: #222; }

  /* Hero */
  .hero-band {
    left: 0; top: 147px; width: 1200px; height: 455px;
    background: linear-gradient(var(--white) 0%, var(--white) 45%, #fdd9db 62%, var(--pink-soft) 100%);
  }
  .hero {
    left: 75px; top: 159px; width: 1050px; height: 439px;
    border: 4px solid #e6e2de;
    background: linear-gradient(100deg, #8a6420 0%, #b78d3e 35%, #a67a2f 60%, #6d4c1c 100%);
  }
  .hero-title { left: 112px; top: 262px; font-size: 64px; font-weight: 700; color: var(--white); }
  .hero-sub { left: 116px; top: 343px; width: 520px; font-size: 22px; font-weight: 600; color: var(--white); line-height: 31px; }
  .hero-dots { left: 115px; top: 528px; display: flex; gap: 9px; }
  .hero-dots span { width: 17px; height: 17px; border-radius: 50%; background: var(--white); }
  .hero-dots span.is-current { background: var(--pink); }

  .btn {
    display: inline-block; width: 142px; height: 45px; line-height: 45px; text-align: center;
    background: linear-gradient(var(--btn-top), var(--btn-bottom));
    color: var(--white); font-size: 14.5px; font-weight: 500; border-radius: 2px;
  }

  .heading { font-size: 25px; font-weight: 500; color: var(--pink); }
  .body-text { font-size: 13.5px; line-height: 24.5px; color: var(--ink); }
  .photo { display: block; }

  /* Welcome */
  .welcome-title { left: 75px; top: 638px; }
  .welcome-text { left: 75px; top: 684px; width: 600px; }
  .welcome-btn { left: 75px; top: 856px; }
  .welcome-photo { left: 704px; top: 645px; width: 422px; height: 256px; background: linear-gradient(135deg, #3b3b3b, #1c1c1c 60%, #4a3b35); }

  /* What we do */
  .services {
    left: 0; top: 956px; width: 1200px; height: 428px;
    background: linear-gradient(#ec7479, var(--pink-soft));
  }
  .services-title { left: 75px; top: 996px; color: var(--white); }
  .services-text { left: 75px; top: 1040px; width: 330px; color: #fde9ea; }
  .services-btn { left: 75px; top: 1283px; }
  .service { top: 1046px; width: 331px; }
  .service .photo { height: 172px; }
  .service h3 { margin-top: 22px; font-size: 15px; font-weight: 600; color: var(--ink); }
  .service p { margin-top: 6px; font-size: 13.5px; line-height: 24.5px; color: #fde9ea; }
  .service-weddings { left: 434px; }
  .service-weddings .photo { background: linear-gradient(135deg, #6a2a8a, #c15ad8 50%, #e9a6f0); }
  .service-corporate { left: 794px; }
  .service-corporate .photo { background: linear-gradient(135deg, #3e3530, #8c7d6e 55%, #5a4d43); }

  /* Events + decor */
  .events-title { left: 75px; top: 1420px; }
  .event { left: 75px; width: 520px; display: flex; gap: 26px; }
  .event .photo { width: 125px; height: 85px; flex: none; }
  .event h4 { font-size: 15px; font-weight: 600; color: var(--ink); margin-top: -2px; }
  .event p { font-size: 13.5px; line-height: 24.5px; margin-top: 4px; }
  .event .more { font-size: 13px; font-weight: 600; color: var(--pink); }
  .event-one { top: 1474px; }
  .event-one .photo { background: linear-gradient(135deg, #8a4b33, #d49a79); }
  .event-two { top: 1596px; }
  .event-two .photo { background: linear-gradient(135deg, #1f3a22, #e8eadf 50%, #2e4d30); }
  .decor-title { left: 613px; top: 1420px; }
  .decor-photo { left: 613px; top: 1474px; width: 179px; height: 206px; background: linear-gradient(160deg, #ece8e4, #9a7255 55%, #d8d2cc); }
  .decor-text { left: 812px; top: 1466px; width: 320px; }
  .decor-btn { left: 812px; top: 1634px; }

  /* Featured */
  .featured { left: 0; top: 1730px; width: 1200px; height: 325px; background: var(--grey-band); }
  .featured-title { left: 0; top: 1756px; width: 1200px; text-align: center; }
  .product { top: 1813px; width: 241px; }
  .product .photo { height: 144px; border: 2px solid #cfcfcf; background: var(--white); position: relative; }
  .product p { margin-top: 18px; font-size: 13.5px; line-height: 25px; color: var(--ink); }
  .product-1 { left: 75px; } .product-2 { left: 345px; } .product-3 { left: 615px; } .product-4 { left: 885px; }
  .product .fill { position: absolute; left: 50%; top: 10px; transform: translateX(-50%); width: 70px; height: 120px; background: linear-gradient(#f2eee6, #b08a3c); }
  .product-3 .fill { width: 100px; height: 136px; top: 2px; background: linear-gradient(#6d7a66, #b7a98f); }

  /* Testimonial */
  .quote-title { left: 0; top: 2092px; width: 1200px; text-align: center; }
  .quote { left: 75px; top: 2149px; width: 1050px; text-align: center; font-size: 13px; font-style: italic; line-height: 24.5px; color: var(--ink); }
  .quote-name { left: 0; top: 2240px; width: 1200px; text-align: center; font-size: 14px; color: var(--pink); }
  .quote-dots { left: 578px; top: 2298px; display: flex; gap: 8px; }
  .quote-dots span { width: 11px; height: 11px; border-radius: 50%; background: #777; }
  .quote-dots span.is-current { background: var(--pink); }

  /* Footer */
  .footer { left: 0; top: 2356px; width: 1200px; height: 151px; background: var(--footer); }
  .footer-nav { left: 75px; top: 2394px; display: flex; gap: 27px; list-style: none; font-size: 12.5px; color: var(--footer-text); }
  .footer-legal { left: 75px; top: 2428px; font-size: 11px; line-height: 21px; color: var(--footer-text); }
  .connect-title { left: 899px; top: 2393px; font-size: 14.5px; color: var(--pink); }
  .social { left: 899px; top: 2429px; display: flex; gap: 8px; }
  .social span { width: 39px; height: 39px; border-radius: 50%; border: 2px solid #9a9a9a; }
</style>
</head>
<body>
  <header>
    <div class="abs brand">Hire a Lantern</div>
    <div class="abs phone">
      <svg width="16" height="16" viewBox="0 0 24 24" aria-hidden="true"><path fill="#ea7479" d="M6.6 10.8a15.1 15.1 0 0 0 6.6 6.6l2.2-2.2a1 1 0 0 1 1-.25 11.4 11.4 0 0 0 3.6.57 1 1 0 0 1 1 1V20a1 1 0 0 1-1 1A17 17 0 0 1 3 4a1 1 0 0 1 1-1h3.5a1 1 0 0 1 1 1c0 1.25.2 2.45.57 3.57a1 1 0 0 1-.25 1z"/></svg>
      123-555-0147
    </div>
    <nav class="abs nav">
      <ul>
        <li class="is-active">Home</li><li>About Us</li><li>Whate We do</li><li>Our Products</li><li>Latest Events</li><li>Blog</li><li>Gallery</li><li>Contact Us</li>
      </ul>
    </nav>
  </header>

  <section>
    <div class="abs hero-band"></div>
    <div class="abs hero" role="img" aria-label="Two white pillar candles glowing on ornate holders against a warm golden background"></div>
    <h1 class="abs hero-title">Hire a Lantern</h1>
    <p class="abs hero-sub">We rent out pillar candles for events such as weddings and corporate events</p>
    <a class="abs btn" style="left:115px;top:431px;">View Products</a>
    <div class="abs hero-dots"><span class="is-current"></span><span></span><span></span><span></span></div>
  </section>

  <section>
    <h2 class="abs heading welcome-title">Welcome to Our Website</h2>
    <p class="abs body-text welcome-text">Aliquam molestie, mi et imperdiet euismod, dui purus auctor tellus, et interdum lacus lectus et ante. Sed accumsan sollicitudin sapien, sit amet adipiscing turpis gravida ac. In congue, neque ac lobortis volutpat, libero mauris varius mi, vitae suscipit ipsum ligula vitae risus. Duis aliquam nibh a dui iaculis viverra id a velit. Vivamus egestas risus in magna varius commodo. Sed semper viverra egestas. Etiam pretium porttitor lectus, vel ornare neque porta volutpat.</p>
    <a class="abs btn welcome-btn">Read More</a>
    <div class="abs photo welcome-photo" role="img" aria-label="White pillar candles on tall candelabra stands with festive floral decor"></div>
  </section>

  <section>
    <div class="abs services"></div>
    <h2 class="abs heading services-title">What We Do</h2>
    <p class="abs body-text services-text">Aliquam molestie, mi et imperdiet euismod, dui purus auctor tellus, et interdum lacus lectus et ante. Sed accumsan sollicitudin sapien, sit amet adipiscing turpis gravida ac. In congue, neque ac lobortis volutpat, libero mauris varius mi, vitae suscipit ipsum ligula vitae risus. Duis aliquam nibh a dui iaculis viverra id a velit. Aenean a nibh eget turpis vehicula tempus ac sed massa. Vestibulum dolor nulla, ultrices acest...</p>
    <a class="abs btn services-btn">Read More</a>
    <div class="abs service service-weddings">
      <div class="photo" role="img" aria-label="Candlelit wedding reception tables in purple light"></div>
      <h3>For Weddings Events</h3>
      <p>Duis aliquam nibh a dui iaculis viverra id a velit. Vivamus egestas risus in magna varius commodo. Sed semper viverra egestas.</p>
    </div>
    <div class="abs service service-corporate">
      <div class="photo" role="img" aria-label="Three lit white pillar candles against a dark wall"></div>
      <h3>For Corporate Events</h3>
      <p>Duis aliquam nibh a dui iaculis viverra id a velit. Vivamus egestas risus in magna varius commodo. Sed semper viverra egestas.</p>
    </div>
  </section>

  <section>
    <h2 class="abs heading events-title">Latest Events</h2>
    <article class="abs event event-one">
      <div class="photo" role="img" aria-label="Candle table setting at a recent event"></div>
      <div><h4>Mar18, 2016</h4><p>Aliquam molestie, mi et imperdiet euismod, dui purus auctor tellus, et interdum lacus lectus et ante.</p><span class="more">Read More</span></div>
    </article>
    <article class="abs event event-two">
      <div class="photo" role="img" aria-label="White pillar candles with green floral arrangements"></div>
      <div><h4>Mar18, 2016</h4><p>Aliquam molestie, mi et imperdiet euismod, dui purus auctor tellus, et interdum lacus lectus et ante.</p><span class="more">Read More</span></div>
    </article>
    <h2 class="abs heading decor-title">Hiring Out Decor</h2>
    <div class="abs photo decor-photo" role="img" aria-label="Faceted amber glass votive holders"></div>
    <p class="abs body-text decor-text">Aliquam molestie, mi et imperdiet euismod, dui purus auctor tellus, et interdum lacus lectus et ante. Sed accumsan sollicitudin sapien, sit amet adipiscing turpis gravida ac. In congue, neque ac lobortis volutpat, libero mauris vitae mi..</p>
    <a class="abs btn decor-btn">Read More</a>
  </section>

  <section>
    <div class="abs featured"></div>
    <h2 class="abs heading featured-title">Featured Candles For Rents</h2>
    <div class="abs product product-1"><div class="photo"><div class="fill" role="img" aria-label="White candle on a brass candlestick"></div></div><p>Aliquam molestie, mi et imperdiet euismod, dui purus</p></div>
    <div class="abs product product-2"><div class="photo"><div class="fill" role="img" aria-label="White candle in a brass chamberstick"></div></div><p>Aliquam molestie, mi et imperdiet euismod, dui purus</p></div>
    <div class="abs product product-3"><div class="photo"><div class="fill" role="img" aria-label="Candle on a stand beside greenery"></div></div><p>Aliquam molestie, mi et imperdiet euismod, dui purus</p></div>
    <div class="abs product product-4"><div class="photo"><div class="fill" role="img" aria-label="Tall taper candle on a brass holder"></div></div><p>Aliquam molestie, mi et imperdiet euismod, dui purus</p></div>
  </section>

  <section>
    <h2 class="abs heading quote-title">What Our Customer Says...</h2>
    <p class="abs quote">" Aliquam molestie, mi et imperdiet euismod, dui purus auctor tellus, et interdum lacus lectus et ante. Sed accumsan sollicitudin sapien, sit amet adipiscing turpis gravida ac. In congue, neque ac lobortis volutpat, libero mauris varius mi, vitae suscipit ipsum ligula vitae risus. Duis aliquam nibh a dui iaculis viverra id a velit. Vivamus egestas risus in magna varius commodo. Sed semper viverra egestas. Etiam pretium porttitor lectus, vel ornare neque porta volutpat..."</p>
    <p class="abs quote-name">-Name Heading</p>
    <div class="abs quote-dots"><span class="is-current"></span><span></span><span></span></div>
  </section>

  <footer>
    <div class="abs footer"></div>
    <ul class="abs footer-nav"><li>Home</li><li>About Us</li><li>Whate We do</li><li>Our Products</li><li>Latest Events</li><li>Blog</li><li>Gallery</li><li>Contact Us</li></ul>
    <p class="abs footer-legal">Copyright © 2016. Company Name All Right Reserved<br>Terms of Uses &nbsp;|&nbsp; Privacy Policy</p>
    <p class="abs connect-title">Connect Us</p>
    <div class="abs social"><span></span><span></span><span></span><span></span><span></span></div>
  </footer>
</body>
</html>
```